Harborlight Amusement Collective (HAC)

We need a business card design for Harborlight Amusement Collective. Modern and sleek looking, with all critical information. Open to single or double sided designs, if double sided info needs to be all on one side. The main Logo is Harborlight Amusement collective and must be on the card. The other three logos are for the brands that fall under the group, they might be good on the back.

Industry/Entity Type

Business

```html
<!DOCTYPE html>
<html lang="en">
<head>
<meta charset="utf-8">
<title>Harborlight Amusement Collective – Business Cards</title>
<link rel="stylesheet" href="https://fonts.googleapis.com/css2?family=Montserrat:wght@400;500;600&family=Open+Sans:wght@400;600&display=swap">
<style>
  :root {
    --stage: #3a302b;
    --card-black: #121212;
    --card-edge: #1c1c1c;
    --band-white: #f4f4f4;
    --brand-blue: #2f6dc4;
    --brand-green: #8db33a;
    --silver: #d2d2d2;
    --text-grey: #bdbdbd;
    --rule: #4a4a4a;
    --sub-dark: #1f2a44;
  }
  * { box-sizing: border-box; margin: 0; padding: 0; }
  html, body { width: 1200px; height: 844px; overflow: hidden; }
  body {
    background: var(--stage);
    font-family: "Open Sans", Arial, sans-serif;
    display: flex;
    align-items: center;
    justify-content: center;
    gap: 44px;
  }
  .card {
    width: 520px;
    height: 300px;
    background: var(--card-black);
    border: 1px solid var(--card-edge);
    position: relative;
    overflow: hidden;
    box-shadow: 0 14px 30px rgba(0,0,0,.45);
  }

  /* Contact side */
  .card--contact { display: flex; }
  .mark-panel {
    width: 46%;
    display: flex;
    align-items: center;
    justify-content: center;
    gap: 12px;
    padding-left: 18px;
  }
  .mark-square { width: 26px; height: 26px; background: var(--brand-blue); flex: none; }
  .mark-name {
    font-family: "Montserrat", Arial, sans-serif;
    font-weight: 600;
    font-size: 15px;
    line-height: 1.25;
    color: var(--brand-blue);
    letter-spacing: .5px;
  }
  .divider {
    width: 1px;
    background: var(--rule);
    margin: 46px 0;
  }
  .details {
    padding: 46px 0 0 26px;
    color: var(--text-grey);
    font-size: 13.5px;
    line-height: 1.45;
  }
  .person-name {
    font-family: "Montserrat", Arial, sans-serif;
    font-size: 19px;
    font-weight: 500;
    letter-spacing: .5px;
    color: var(--brand-blue);
    line-height: 1.1;
  }
  .person-name .surname { color: var(--brand-green); }
  .person-role { font-size: 13px; margin-bottom: 6px; }
  .contact-list { list-style: none; }
  .contact-list li { display: flex; align-items: center; gap: 8px; }
  .contact-list svg { width: 11px; height: 11px; fill: var(--brand-blue); flex: none; }
  .address { margin-top: 6px; padding-left: 19px; }

  /* Brand side */
  .card--brand { display: flex; flex-direction: column; }
  .brand-top {
    flex: 1;
    display: flex;
    flex-direction: column;
    align-items: center;
    justify-content: center;
    gap: 14px;
  }
  .brand-square { width: 40px; height: 40px; background: var(--silver); }
  .brand-name {
    font-family: "Montserrat", Arial, sans-serif;
    font-weight: 500;
    font-size: 19px;
    letter-spacing: 1.5px;
    color: var(--silver);
    text-transform: uppercase;
  }
  .brand-rule { display: flex; align-items: center; gap: 12px; }
  .brand-rule span { width: 70px; height: 1px; background: var(--silver); }
  .brand-rule em {
    font-style: normal;
    font-family: "Montserrat", Arial, sans-serif;
    font-size: 13px;
    letter-spacing: 7px;
    color: var(--silver);
  }
  .sub-brands {
    height: 78px;
    background: var(--band-white);
    display: flex;
    align-items: center;
    justify-content: space-around;
    padding: 0 14px;
  }
  .sub-brand {
    display: flex;
    align-items: center;
    gap: 7px;
    font-family: "Montserrat", Arial, sans-serif;
    font-weight: 600;
    font-size: 14px;
    color: var(--sub-dark);
  }
  .sub-dot { width: 14px; height: 14px; border-radius: 50%; flex: none; }
  .sub-dot--blue { background: var(--brand-blue); }
  .sub-dot--green { background: var(--brand-green); }
  .sub-dot--navy { background: var(--sub-dark); }
</style>
</head>
<body>

  <section class="card card--contact">
    <div class="mark-panel">
      <span class="mark-square"></span>
      <span class="mark-name">Harborlight<br>Amusement<br>Collective</span>
    </div>
    <div class="divider"></div>
    <div class="details">
      <p class="person-name">MARCUS <span class="surname">ELLERY</span></p>
      <p class="person-role">Managing Director</p>
      <ul class="contact-list">
        <li><svg viewBox="0 0 12 12"><path d="M1 3c0-1 1-2 2-2h6c1 0 2 1 2 2v1H8V3H4v1H1zM2 5h8l1 6H1z"/></svg>055-987 210 436</li>
        <li><svg viewBox="0 0 12 12"><path d="M3 0h6v12H3zM4 1v8h4V1z"/></svg>055-987 210 437</li>
        <li><svg viewBox="0 0 12 12"><path d="M0 2h12v1L6 7 0 3zM0 4l6 4 6-4v6H0z"/></svg>hello@harborlighthac.com</li>
        <li><svg viewBox="0 0 12 12"><circle cx="6" cy="6" r="5.5"/></svg>www.harborlighthac.com</li>
      </ul>
      <p class="address">48 Quayside Lane, Suite 3<br>Marlow Bay, 204518.</p>
    </div>
  </section>

  <section class="card card--brand">
    <div class="brand-top">
      <span class="brand-square"></span>
      <p class="brand-name">Harborlight Amusement Collective</p>
      <div class="brand-rule"><span></span><em>HAC</em><span></span></div>
    </div>
    <div class="sub-brands">
      <span class="sub-brand"><span class="sub-dot sub-dot--navy"></span>Bleacher Hospitality</span>
      <span class="sub-brand"><span class="sub-dot sub-dot--green"></span>Tidewave Tickets</span>
      <span class="sub-brand"><span class="sub-dot sub-dot--blue"></span>gatepass</span>
    </div>
  </section>

</body>
</html>
```